Call Center In Need of Website Design

We are a call center that provides inbound and outbound calling & marketing services for eCommerce store. We would like to see a fun, creative, playful design that is simple.

Here are some sample design sites we like;
- https://www.velmoreline.com/
- https://pindrask.io/
- https://www.glimbertic.com/live-chat-software/
- https://www.zavrolin.com/

Here are some competitor sites;
- https://www.ostrevaglinks.com/
- https://www.helpkestrel.com/

I have attached website content for your use.

Target Market(s)

eCommerce

Coding

Coded - Design and coding required

Number of Pages Required

5+ page

Font styles to use
Sans Serif

Colors

Designer to choose colors to be used in the design.

Requirements
Must have
• Must have designs for the following 5 separate pages;
• 1. Home (landing)
• - This will be were the design style really needs to show.
• - Just needs to touch on key services
• - CTA
• 2. About Us
• - Basic page for about me paragraph
• 3. Services
• - List of services with icons
• - Click on service type to expand details or hover over service icon to view popup bubble with details about that service
• 4. Pricing
• - Option to bundle 1(one) digital service plan and 1(one) call center service plan
• - Bundling adds 10% monthly discount to over all price
• - Customer does NOT have to bundle
• - FAQ
• 5. Contact Us
• - Include a capture form (name, company name, email, phone, message)
• - Contact info
• - Business hours
• When customer purchases their desired plan, then they are taken to a page where they must schedule a call with an account rep.
Nice to have
• home page animations
Should not have
• All information on Home/Landing page.

```html
<!DOCTYPE html>
<html lang="en">
<head>
<meta charset="utf-8">
<title>Orbitra — Omnichannel Customer Care</title>
<link rel="stylesheet" href="https://fonts.googleapis.com/css2?family=Oswald:wght@500;700&family=Montserrat:wght@400;500;600;700&display=swap">
<style>
:root{
  --navy:#3a3a82;
  --navy-deep:#2f2f70;
  --mint:#67c6ad;
  --mint-light:#7dd9c1;
  --mint-field:#86dcc6;
  --white:#ffffff;
  --grey:#ececf1;
  --ink:#55557a;
  --line:#a9a9b8;
}
*{box-sizing:border-box;margin:0;padding:0}
html,body{width:1200px;height:2791px;overflow:hidden;background:var(--white)}
body{font-family:"Montserrat",Arial,sans-serif;color:var(--navy)}
.page{position:relative;width:1200px;height:2791px;overflow:hidden}
.abs{position:absolute}

/* hero */
.hero{left:0;top:0;width:1200px;height:420px;background:var(--navy)}
.brand{left:164px;top:30px;display:flex;align-items:center;gap:16px;color:var(--white);font-size:34px;font-weight:500;letter-spacing:6px}
.brand-dot{width:44px;height:44px;border-radius:50%;border:4px solid var(--mint)}
.nav{left:563px;top:44px;display:flex;gap:36px;font-size:11px;font-weight:600;letter-spacing:.6px;color:var(--white);text-transform:uppercase}
.nav a{color:inherit;text-decoration:none;position:relative}
.nav .current::after{content:"";position:absolute;left:0;right:0;bottom:-10px;height:2px;background:var(--white)}
.hero-title{left:160px;top:150px;font-family:"Oswald",Impact,sans-serif;font-weight:700;font-size:60px;line-height:70px;color:var(--white)}
.hero-sub{left:162px;top:300px;font-size:17px;letter-spacing:4.2px;color:var(--white)}
.rocket-art{left:50px;top:100px;width:50px;height:280px;background:linear-gradient(var(--mint),rgba(103,198,173,.2));border-radius:25px 25px 4px 4px}
.astronaut-art{left:790px;top:90px;width:410px;height:290px;background:radial-gradient(circle at 60% 40%,#e8e8f3,#8d8dc0 70%);border-radius:50% 50% 0 0;opacity:.9}
.cloud-band{left:0;top:360px;width:1200px;height:60px;background:linear-gradient(var(--navy),var(--mint) 85%)}

/* what we do */
.intro{left:0;top:420px;width:1200px;height:311px;background:var(--mint)}
.flag-art{left:6px;top:540px;width:150px;height:190px;background:linear-gradient(#8ed8c4,#4fae96);border-radius:12px}
.section-mark{display:inline-block;width:34px;height:3px;background:var(--white);position:relative;margin-right:12px;vertical-align:middle}
.section-mark::before{content:"";position:absolute;left:8px;top:-7px;width:26px;height:3px;background:var(--white)}
.intro-title{left:278px;top:518px;font-family:"Oswald",Impact,sans-serif;font-size:29px;font-weight:700;color:var(--white)}
.intro-copy{left:325px;top:570px;width:570px;font-size:11px;line-height:22px;color:var(--white)}
.intro-copy strong{font-weight:600}

/* services */
.services-head{left:0;top:790px;width:1200px;text-align:center}
.services-head .bar{display:block;margin:0 auto 10px;width:34px;height:3px;background:var(--navy);box-shadow:0 -7px 0 -1px var(--navy)}
.services-head h2{font-family:"Oswald",Impact,sans-serif;font-size:31px;font-weight:700}
.group-title{left:0;width:1200px;text-align:center;font-family:"Oswald",Impact,sans-serif;font-size:18px;font-weight:700;text-decoration:underline;text-underline-offset:4px;color:var(--navy)}
.group-title-light{color:var(--white)}
.tree{left:0;width:1200px}
.tile{position:absolute;width:134px;height:86px;border-radius:3px;display:flex;flex-direction:column;align-items:center;justify-content:center;gap:8px;font-size:11.5px;font-weight:600;text-align:center;line-height:13px}
.tile svg{width:30px;height:30px}
.tile-digital{background:var(--navy);color:var(--white);box-shadow:0 4px 8px rgba(0,0,0,.25)}
.tile-call{background:var(--white);color:var(--navy);box-shadow:0 4px 8px rgba(0,0,0,.3)}
.call{left:0;top:1190px;width:1200px;height:754px;background:var(--navy)}
.tooltip{position:absolute;left:249px;top:1704px;width:134px;height:182px;background:var(--grey);border-radius:0 0 3px 3px;padding:16px 10px;font-size:10.5px;line-height:18px;text-align:center;color:var(--ink)}

/* cta */
.cta-title{left:0;top:2050px;width:1200px;text-align:center;font-family:"Oswald",Impact,sans-serif;font-weight:700;font-size:46px;line-height:54px;letter-spacing:1px}
.cta-btn{left:520px;top:2184px;width:160px;height:45px;border-radius:23px;background:var(--mint);color:var(--white);font-size:11px;font-weight:600;display:flex;align-items:center;justify-content:center;letter-spacing:.5px}
.launch-art{left:940px;top:2074px;width:260px;height:264px;background:radial-gradient(ellipse at 50% 30%,#8fe0c9,#67c6ad 65%);border-radius:50% 50% 0 0}

/* contact */
.contact{left:0;top:2338px;width:1200px;height:344px;background:var(--mint)}
.contact-card{left:186px;top:2398px;width:275px;height:232px;background:var(--mint-light);box-shadow:0 6px 14px rgba(0,0,0,.15);padding:26px 24px;color:var(--white);font-size:11.5px}
.contact-card h3{font-size:14px;font-weight:600;margin-bottom:8px}
.contact-card .rule{width:30px;height:2px;background:var(--white);margin-bottom:20px}
.contact-row{display:flex;gap:14px;margin-bottom:16px;line-height:17px}
.contact-row svg{flex:none;width:12px;height:12px;margin-top:3px}
.callback-title{left:487px;top:2396px;font-size:28px;font-weight:600;color:var(--white)}
.field{position:absolute;width:253px;height:36px;background:var(--mint-field);border:1px solid rgba(255,255,255,.5);font-size:10px;color:var(--white);padding:0 14px;display:flex;align-items:center}
.submit{left:487px;top:2582px;width:104px;height:39px;border:2px solid var(--white);border-radius:4px;color:var(--white);font-size:11px;font-weight:600;display:flex;align-items:center;justify-content:center}

/* footer */
.copyright{left:160px;top:2716px;font-size:11px;line-height:18px;color:#555}
.foot-nav{left:412px;top:2728px;display:flex;gap:28px;font-size:11.5px;color:#555}
.foot-nav .current{color:var(--mint)}
.social{left:919px;top:2722px;display:flex;gap:6px}
.social span{width:26px;height:26px;border-radius:3px;background:var(--navy)}
</style>
</head>
<body>
<div class="page">

  <!-- hero -->
  <section class="abs hero"></section>
  <div class="abs rocket-art" role="img" aria-label="Illustration of a small rocket lifting off with a long trail"></div>
  <div class="abs astronaut-art" role="img" aria-label="Illustration of an astronaut floating among stars"></div>
  <div class="abs cloud-band" role="img" aria-label="Illustration of soft mint clouds along the bottom of the hero"></div>
  <div class="abs brand"><span class="brand-dot"></span>ORBITRA</div>
  <nav class="abs nav">
    <a class="current">Home</a><a>About Us</a><a>Services</a><a>Pricing</a><a>Contact Us</a><a>Account</a>
  </nav>
  <h1 class="abs hero-title">Orbitra Is An<br>Omnichannel</h1>
  <p class="abs hero-sub">Provider For Customer Care</p>

  <!-- what we do -->
  <section class="abs intro"></section>
  <div class="abs flag-art" role="img" aria-label="Illustration of an astronaut waving beside a planted flag"></div>
  <h2 class="abs intro-title"><span class="section-mark"></span>WHAT WE DO</h2>
  <p class="abs intro-copy">Orbitra is your personal customer service and product research team. We love eCommerce, but we love seeing business owners succeed even more! That is exactly why we have developed the processes and technology to take care of the most over looked areas in eCommerce - Customer Service and Retention. Let Orbitra handle your customers while you focus on growing your business.<br><strong>Let Orbitra handle your customers while you focus on growing your business.</strong></p>

  <!-- services -->
  <div class="abs services-head"><span class="bar"></span><h2>Services</h2></div>
  <h3 class="abs group-title" style="top:868px">DIGITAL SERVICES</h3>
  <svg class="abs tree" style="top:910px;height:130px" viewBox="0 0 1200 130" aria-hidden="true">
    <g stroke="#a9a9b8" stroke-width="2" stroke-dasharray="3 4" fill="none">
      <path d="M600 0V68M242 68H957M242 68V118M385 68V118M528 68V118M671 68V118M814 68V118M957 68V118"/>
    </g>
    <g fill="#a9a9b8">
      <path d="M594 56h12l-6 9z"/><path d="M236 118h12l-6 9z"/><path d="M379 118h12l-6 9z"/><path d="M522 118h12l-6 9z"/><path d="M665 118h12l-6 9z"/><path d="M808 118h12l-6 9z"/><path d="M951 118h12l-6 9z"/>
    </g>
  </svg>
  <div class="tile tile-digital" style="left:175px;top:1040px"><svg viewBox="0 0 30 30" fill="none" stroke="#fff" stroke-width="2"><rect x="3" y="8" width="24" height="16"/><path d="M3 8l12 9 12-9"/></svg>Email Support</div>
  <div class="tile tile-digital" style="left:318px;top:1040px"><svg viewBox="0 0 30 30" fill="#fff"><path d="M4 6h22v14H12l-6 5v-5H4z"/></svg>Live Chat Support</div>
  <div class="tile tile-digital" style="left:461px;top:1040px"><svg viewBox="0 0 30 30" fill="none" stroke="#fff" stroke-width="2"><path d="M15 4l11 5v12l-11 5-11-5V9z"/><path d="M4 9l11 5 11-5M15 14v12"/></svg>Product Research</div>
  <div class="tile tile-digital" style="left:604px;top:1040px"><svg viewBox="0 0 30 30" fill="none" stroke="#fff" stroke-width="2"><rect x="6" y="3" width="18" height="24"/><path d="M10 9h10M10 14h10M10 19h10"/></svg>Product Listing</div>
  <div class="tile tile-digital" style="left:747px;top:1040px"><svg viewBox="0 0 30 30" fill="none" stroke="#fff" stroke-width="2"><rect x="3" y="5" width="20" height="16"/><circle cx="20" cy="19" r="5"/><path d="M24 23l4 4"/></svg>Price Monitoring</div>
  <div class="tile tile-digital" style="left:890px;top:1040px"><svg viewBox="0 0 30 30" fill="none" stroke="#fff" stroke-width="2"><rect x="4" y="8" width="22" height="18"/><path d="M4 8l4-5h14l4 5"/><circle cx="15" cy="17" r="4"/></svg>Product Photo &amp;<br>Video Editing</div>

  <!-- call center -->
  <section class="abs call"></section>
  <h3 class="abs group-title group-title-light" style="top:1236px">CALL CENTER SERVICES</h3>
  <svg class="abs tree" style="top:1276px;height:345px" viewBox="0 0 1200 345" aria-hidden="true">
    <g stroke="#ffffff" stroke-width="2" stroke-dasharray="3 4" fill="none">
      <path d="M600 0V282M242 73H957M242 73V120M385 73V120M528 73V120M671 73V120M814 73V120M957 73V120"/>
      <path d="M316 288H884M316 288V334M458 288V334M742 288V334M884 288V334"/>
    </g>
    <g fill="#ffffff">
      <path d="M594 58h12l-6 9z"/><path d="M236 120h12l-6 9z"/><path d="M379 120h12l-6 9z"/><path d="M522 120h12l-6 9z"/><path d="M665 120h12l-6 9z"/><path d="M808 120h12l-6 9z"/><path d="M951 120h12l-6 9z"/>
      <path d="M310 334h12l-6 9z"/><path d="M452 334h12l-6 9z"/><path d="M594 334h12l-6 9z"/><path d="M736 334h12l-6 9z"/><path d="M878 334h12l-6 9z"/>
    </g>
  </svg>
  <div class="tile tile-call" style="left:175px;top:1404px"><svg viewBox="0 0 30 30" fill="none" stroke="#3a3a82" stroke-width="2.4"><path d="M6 18v-4a9 9 0 0118 0v4"/><rect x="4" y="17" width="5" height="8" fill="#3a3a82"/><rect x="21" y="17" width="5" height="8" fill="#3a3a82"/></svg>Answering service</div>
  <div class="tile tile-call" style="left:318px;top:1404px"><svg viewBox="0 0 30 30"><circle cx="15" cy="15" r="12" fill="#3a3a82"/><path d="M11 9l3 3-2 2a8 8 0 004 4l2-2 3 3-2 2c-5 0-10-5-10-10z" fill="#fff"/></svg>Welcome Calls</div>
  <div class="tile tile-call" style="left:461px;top:1404px"><svg viewBox="0 0 30 30" fill="#3a3a82"><circle cx="13" cy="9" r="6"/><path d="M2 28c0-7 5-11 11-11 3 0 5 1 6 2v9z"/><circle cx="23" cy="23" r="6"/><path d="M20 23l2 2 4-4" stroke="#fff" stroke-width="2" fill="none"/></svg>Follow-Up Service</div>
  <div class="tile tile-call" style="left:604px;top:1404px"><svg viewBox="0 0 30 30" fill="#3a3a82"><rect x="4" y="20" width="4" height="7"/><rect x="11" y="15" width="4" height="12"/><rect x="18" y="10" width="4" height="17"/><rect x="25" y="5" width="3" height="22"/></svg>Customer Upselling</div>
  <div class="tile tile-call" style="left:747px;top:1404px"><svg viewBox="0 0 30 30" fill="none" stroke="#3a3a82" stroke-width="2.4"><rect x="8" y="3" width="14" height="24" rx="2"/><path d="M12 12l2 2 4-4"/></svg>Over-The-Phone<br>Order Taking</div>
  <div class="tile tile-call" style="left:890px;top:1404px"><svg viewBox="0 0 30 30" fill="#3a3a82"><path d="M6 5l6 6-3 3a14 14 0 007 7l3-3 6 6-4 4C12 28 2 18 2 9z"/><path d="M17 4a10 10 0 019 9M17 9a5 5 0 014 4" stroke="#3a3a82" stroke-width="2" fill="none"/></svg>Feedback/<br>Survey Calls</div>

  <div class="tile tile-call" style="left:249px;top:1618px"><svg viewBox="0 0 30 30" fill="none" stroke="#3a3a82" stroke-width="2.4"><rect x="3" y="10" width="24" height="16"/><path d="M3 10l12 9 12-9"/></svg>Message Delivering<br>Service</div>
  <div class="tooltip">Orbitra is your personal customer service and product research team. We love eCommerce, but we love seeing business owners succeed even more!</div>
  <div class="tile tile-call" style="left:391px;top:1618px"><svg viewBox="0 0 30 30" fill="none" stroke="#3a3a82" stroke-width="2.4"><rect x="6" y="4" width="18" height="23"/><path d="M10 11l2 2 3-3M17 12h4M10 19l2 2 3-3M17 20h4"/></svg>ROI Diagnostics<br>&amp; Reporting</div>
  <div class="tile tile-call" style="left:533px;top:1618px"><svg viewBox="0 0 30 30" fill="#3a3a82"><circle cx="15" cy="11" r="7"/><path d="M3 28c0-7 5-10 12-10s12 3 12 10z"/></svg>Scalable Call<br>Center Pricing</div>
  <div class="tile tile-call" style="left:675px;top:1618px"><svg viewBox="0 0 30 30" fill="none" stroke="#3a3a82" stroke-width="3"><path d="M5 5l20 20M25 5L5 25"/></svg>Customizable For<br>Any Industry</div>
  <div class="tile tile-call" style="left:817px;top:1618px"><svg viewBox="0 0 30 30" fill="#3a3a82"><path d="M15 3a10 10 0 00-10 10c0 4 2 6 3 8v6h10v-3h4v-5h3l-3-6A10 10 0 0015 3z"/></svg>100% US-Based<br>Agents</div>

  <!-- cta -->
  <h2 class="abs cta-title">READY TO TAKE YOUR BUSINESS<br>TO THE NEXT LEVEL</h2>
  <div class="abs cta-btn">GET STARTED</div>
  <div class="abs launch-art" role="img" aria-label="Illustration of a rocket launching from a cloud of smoke"></div>

  <!-- contact -->
  <section class="abs contact" role="img" aria-label="Faint moon landscape with astronaut in mint tones"></section>
  <div class="abs contact-card">
    <h3>Contact Details</h3>
    <div class="rule"></div>
    <div class="contact-row"><svg viewBox="0 0 12 12" fill="#fff"><path d="M2 1l3 3-1.5 1.5a6 6 0 003 3L8 7l3 3-2 2C5 12 0 7 0 3z"/></svg>Phone: (800) 555-0147</div>
    <div class="contact-row"><svg viewBox="0 0 12 12" fill="#fff"><path d="M0 2h12v1L6 7 0 3zM0 4.5l6 4 6-4V10H0z"/></svg>hello@orbitra.co</div>
    <div class="contact-row"><svg viewBox="0 0 12 12" fill="#fff"><path d="M6 0a4 4 0 014 4c0 3-4 8-4 8S2 7 2 4a4 4 0 014-4zm0 2.5a1.5 1.5 0 100 3 1.5 1.5 0 000-3z"/></svg><span>Orbitra, Inc.<br>418 Larkmoor Ave, Dunmere, CA 90000</span></div>
  </div>
  <h2 class="abs callback-title">Request For Call Back</h2>
  <div class="field" style="left:487px;top:2472px">Name</div>
  <div class="field" style="left:757px;top:2472px">Email</div>
  <div class="field" style="left:487px;top:2524px">Ph Num</div>
  <div class="field" style="left:757px;top:2524px">Enquiry About</div>
  <div class="abs submit">Submit Now</div>

  <!-- footer -->
  <p class="abs copyright">Copyright © 2018<br>All rights reserved</p>
  <nav class="abs foot-nav"><span class="current">Home</span><span>About Us</span><span>Service</span><span>Pricing</span><span>Contact Us</span><span>Account</span></nav>
  <div class="abs social" aria-label="Social links"><span></span><span></span><span></span><span></span></div>
</div>
</body>
</html>
```